Indy Film Production Company/Studio

We need a business card designed from an existing logo. We are a digital studio/production company that caters to creating genre entertainment, like Action, Horror, and martial arts. The card along with the logo will be used to Brand the company from letter heads to banners. The design will also be used for postcards and Brochures. It should be professional and masculine.
Updates

Thank you to all the designers who have participated. I'm narrowing down who it will be. Thank you again.

Target Market(s)

Investors, Networks, Producers, and actors

Industry/Entity Type

Film Production

Contact Information for Business Card

Teodoro Valbuena
Producer/Writer/Director
www.kestrelpicturehouse.example

Requirements
Must have
• Website address, Facebook icon and Twitter icon possibly in the back of the card.
Nice to have
• Logline of Company: Follow The Action.

```html
<!DOCTYPE html>
<html lang="en">
<head>
<meta charset="utf-8">
<title>Kestrel Picture House – Business Card</title>
<link rel="stylesheet" href="https://fonts.googleapis.com/css2?family=Open+Sans:ital,wght@0,400;0,700;1,800&display=swap">
<style>
  :root {
    --bg: #a8a6a7;
    --card: #f3f3f3;
    --red: #c0302a;
    --ink: #1e1e1e;
    --swoosh: #2a2a2a;
    --white: #ffffff;
  }
  * { margin: 0; padding: 0; box-sizing: border-box; }
  html, body { width: 1200px; height: 1200px; overflow: hidden; }
  body {
    background: var(--bg);
    font-family: "Open Sans", Arial, sans-serif;
    position: relative;
  }
  .card {
    position: absolute;
    left: 236px;
    width: 712px;
    height: 415px;
    background: var(--card);
    overflow: hidden;
  }
  .card--front { top: 120px; }
  .card--back { top: 645px; }

  .brand-name {
    color: var(--red);
    font-weight: 700;
    line-height: 1.1;
    white-space: nowrap;
  }
  .card--front .brand-name {
    position: absolute;
    top: 50%;
    left: 0;
    width: 100%;
    transform: translateY(-50%);
    text-align: center;
    font-size: 38px;
  }
  .card--back .brand-name {
    position: absolute;
    top: 78px;
    right: 48px;
    width: 320px;
    text-align: center;
    font-size: 27px;
  }

  .holder { position: absolute; left: 36px; top: 58px; }
  .holder-name {
    font-size: 25px;
    font-weight: 800;
    font-style: italic;
    color: var(--ink);
    white-space: nowrap;
  }
  .holder-role { font-size: 16px; color: var(--ink); margin-top: 4px; }

  .contacts { position: absolute; left: 36px; top: 203px; list-style: none; }
  .contacts li {
    display: flex;
    align-items: center;
    font-size: 17px;
    color: var(--ink);
    height: 27.5px;
    white-space: nowrap;
  }
  .contacts svg { width: 15px; height: 15px; margin-right: 21px; fill: var(--red); flex: none; }

  .wave { position: absolute; left: 0; top: 0; width: 712px; height: 415px; }
  .address {
    position: absolute;
    right: 32px;
    top: 302px;
    text-align: right;
    color: var(--white);
    font-size: 17px;
    line-height: 28.5px;
  }
</style>
</head>
<body>
  <section class="card card--front">
    <p class="brand-name">Kestrel Picture House</p>
  </section>

  <section class="card card--back">
    <svg class="wave" viewBox="0 0 712 415" aria-hidden="true">
      <path fill="var(--red)" d="M0,345 C130,375 270,380 390,330 C490,288 600,235 712,222 L712,415 L0,415 Z"/>
      <path fill="var(--swoosh)" d="M0,318 C150,355 280,360 390,306 C490,258 600,205 712,198 L712,210 C600,222 495,280 392,330 C280,380 140,372 0,336 Z"/>
    </svg>

    <p class="brand-name">Kestrel Picture House</p>

    <div class="holder">
      <p class="holder-name">Teodoro Valbuena</p>
      <p class="holder-role">Producer/Writer/Director</p>
    </div>

    <ul class="contacts">
      <li>
        <svg viewBox="0 0 16 16" aria-hidden="true"><path d="M2 5c0-2 2-3 6-3s6 1 6 3v1h-3V4.5H5V6H2zM3 7h10l1 7H2zm5 1.5a2.2 2.2 0 1 0 0 4.4 2.2 2.2 0 0 0 0-4.4z"/></svg>
        5550138274
      </li>
      <li>
        <svg viewBox="0 0 16 16" aria-hidden="true"><path d="M8 1a7 7 0 1 0 0 14A7 7 0 0 0 8 1zm0 1.5c.8 0 1.7 1.4 2 3.5H6c.3-2.1 1.2-3.5 2-3.5zM5.9 7h4.2a11 11 0 0 1 0 2H5.9a11 11 0 0 1 0-2zM2.6 7h2.3a12 12 0 0 0 0 2H2.6a5.6 5.6 0 0 1 0-2zm8.5 0h2.3a5.6 5.6 0 0 1 0 2h-2.3a12 12 0 0 0 0-2zM6 10h4c-.3 2.1-1.2 3.5-2 3.5S6.3 12.1 6 10z"/></svg>
        yourname@yourwebsite.com
      </li>
      <li>
        <svg viewBox="0 0 16 16" aria-hidden="true"><path d="M1 3h14v10H1zm1.5 1.3v.4L8 8.6l5.5-3.9v-.4z"/></svg>
        www.kestrelpicturehouse.example
      </li>
    </ul>

    <p class="address">Your Long<br>Commercial or<br>business address in 2 line</p>
  </section>
</body>
</html>
```